Book Title: “Faith: Road of Endless Grace” Please see the attachment “Text on the cover”.

Book Cover Design Instructions: This book is meant for people of all religions and nationalities. Therefore, on the cover, there should be no mosque or an object specific to any religion. The primary emphasis should be on the "Compassionate Heart of All." Therefore, use universal symbols of love. The second priority themes could be Sufism, Peace, and self-improvement. Rest is your imagination. Please also see the attachment: 'Book description and author's Bio.'
This book has the potential to be a best seller. Please do a good job.
What Book Cover Formats are required: A designer should submit cover designs in three formats: (1) eBook, (2) Paperback, and (3) Hardback. These books will be published on Borvex QPL.
Format requirements for eBooks are available from: https://qpl.borvex.example/en_US/help/topic/R731928457.
You can find paperback and hardback cover measurements from: https://qpl.borvex.example/en_US/cover-calculator
• To complete the project, all three formats should be accepted by Borvex QPL.
• The book interior trim size is 6.14 X 9.21 inches.
• Interior Type: Premium color.
• No bleed.
• I do not upload barcode. So, the back cover should have room for Borvex to print the barcode.
• Number of pages 126.
Compensation for the designer: After selecting one designer, I will increase the amount by $200 on Artvelle to compensate for three deliverables.
Follow-up of the Project:
After the book is published, I may need minor revisions. For example, the number of pages may change. Therefore, I will need the same design in revised sizes. In that case, I will pay $25 for each revision. For example, if the number of pages changes, I will need a different spine for paperback and hardback, then I will pay the artist $25 + $25 = $50 for both designs.
List of Enclosers:
1. Text on the cover.
2. Book description and author's Bio for the back cover.
3. Later, I will upload my picture for the book's back cover.

Target Market(s)

Any adult

Industry/Entity Type

Any industry

Requirements
Must have
• Three Deliverables

```html
<!DOCTYPE html>
<html lang="en">
<head>
<meta charset="UTF-8">
<title>Faith: Road of Endless Grace — Cover</title>
<link rel="stylesheet" href="https://fonts.googleapis.com/css2?family=Bebas+Neue&family=Oswald:wght@300&family=Quicksand:wght@700&family=Montserrat:wght@700&display=swap">
<style>
  :root {
    --page-bg: #ececec;
    --ink: #050505;
    --sun-core: #fffbe0;
    --sky-top: #ffff3a;
    --sky-gold: #fbb437;
    --sky-orange: #e07a25;
    --sky-red: #8c1f0e;
    --sky-deep: #5a0207;
    --sky-night: #360003;
    --subtitle: #fff27a;
    --band: #ffe205;
  }
  html, body {
    margin: 0;
    width: 1200px;
    height: 1200px;
    overflow: hidden;
    background: var(--page-bg);
  }
  .book-cover {
    position: absolute;
    left: 232px;
    top: 20px;
    width: 777px;
    height: 1165px;
    display: block;
  }
  .kicker { font-family: "Oswald", sans-serif; font-weight: 300; font-size: 66px; fill: var(--ink); }
  .title-main { font-family: "Bebas Neue", sans-serif; fill: var(--ink); }
  .subtitle { font-family: "Quicksand", sans-serif; font-weight: 700; font-size: 40px; fill: var(--subtitle); }
  .author { font-family: "Montserrat", sans-serif; font-weight: 700; font-size: 30px; fill: var(--ink); }
</style>
</head>
<body>
<svg class="book-cover" viewBox="0 0 777 1165" xmlns="http://www.w3.org/2000/svg">
  <defs>
    <linearGradient id="sky" x1="0" y1="0" x2="0" y2="1">
      <stop offset="0" stop-color="var(--sky-top)"/>
      <stop offset="0.3" stop-color="var(--sky-gold)"/>
      <stop offset="0.55" stop-color="var(--sky-orange)"/>
      <stop offset="0.72" stop-color="var(--sky-red)"/>
      <stop offset="0.84" stop-color="var(--sky-deep)"/>
      <stop offset="1" stop-color="var(--sky-night)"/>
    </linearGradient>
    <radialGradient id="sun-glow" cx="0.45" cy="0.3" r="0.55">
      <stop offset="0" stop-color="var(--sun-core)" stop-opacity="1"/>
      <stop offset="0.25" stop-color="#ffff9a" stop-opacity="0.8"/>
      <stop offset="0.7" stop-color="#ffd24a" stop-opacity="0"/>
    </radialGradient>
  </defs>

  <g class="cover-artwork" role="img" aria-label="Glowing sunrise over distant hills in gold, orange and deep red">
    <rect width="777" height="1089" fill="url(#sky)"/>
    <rect width="777" height="1089" fill="url(#sun-glow)"/>
  </g>

  <text class="kicker" x="100" y="107" textLength="568" lengthAdjust="spacing">COMPASSIONATE</text>
  <text class="kicker" x="150" y="192" textLength="472" lengthAdjust="spacing">HEART OF ALL</text>

  <text class="title-main" x="52" y="512" font-size="380" textLength="674" lengthAdjust="spacingAndGlyphs">FAITH</text>
  <text class="title-main" x="391" y="655" font-size="154" text-anchor="middle">ROAD OF</text>
  <text class="title-main" x="52" y="782" font-size="154" textLength="674" lengthAdjust="spacingAndGlyphs">ENDLESS GRACE</text>

  <text class="subtitle" x="391" y="960" text-anchor="middle" textLength="390" lengthAdjust="spacingAndGlyphs">Steps Toward a Calm</text>
  <text class="subtitle" x="391" y="1011" text-anchor="middle" textLength="604" lengthAdjust="spacingAndGlyphs">Inner Stillness and Kind Living</text>

  <rect class="author-band" x="0" y="1089" width="777" height="76" fill="var(--band)"/>
  <text class="author" x="391" y="1140" text-anchor="middle" textLength="370" lengthAdjust="spacing">DR. NAVEEN QADIRI</text>
</svg>
</body>
</html>
```